Business cards - BRENT Roofing & Siding

We need simple business cards made up for our Roofing & Siding business based in Calgary Alberta.
The logo on one side of the card and potentially our slogan "Raised with care, proven by years".
The other side could have:
-A small logo
-Rep name:
-Rep cell phone:
-Rep email:
-Office phone: 403-684-2093
-Website: PrairieShingleWorks.com

We would like to incorporate the colours from our logo, especially the lite blue on the jpeg file. I have attached the ai file and jpeg file. We like the colours better on the jpeg file.

I do not require a money back guarantee

```html
<!DOCTYPE html>
<html lang="en">
<head>
<meta charset="utf-8">
<title>BRENT Roofing &amp; Siding – Business Cards</title>
<link rel="stylesheet" href="https://fonts.googleapis.com/css2?family=Lato:wght@400;700&family=Montserrat:wght@500;600&display=swap">
<style>
  :root {
    --sky-blue: #0a8cf0;
    --deep-blue: #0568bf;
    --maple-red: #e8202a;
    --ink: #333333;
    --card-white: #ffffff;
    --card-black: #1b1b1b;
    --silver: #b9b9b9;
    --backdrop: #e6e6e4;
  }
  * { margin: 0; padding: 0; box-sizing: border-box; }
  html, body { width: 1200px; height: 802px; overflow: hidden; }
  body {
    background: var(--backdrop);
    font-family: "Lato", Arial, sans-serif;
    position: relative;
  }
  .card {
    position: absolute;
    top: 236px;
    width: 540px;
    height: 320px;
    border-radius: 4px;
    overflow: hidden;
    box-shadow: 0 6px 18px rgba(0,0,0,0.18);
  }
  .card--front { left: 40px; background: var(--card-white); }
  .card--back { left: 620px; background: var(--card-black); }

  /* front: contact side */
  .rep {
    position: absolute;
    top: 34px;
    right: 36px;
    text-align: right;
  }
  .rep__name {
    font-size: 30px;
    font-weight: 400;
    letter-spacing: 1px;
    color: var(--sky-blue);
    text-transform: uppercase;
    line-height: 1;
  }
  .rep__title {
    font-size: 17px;
    color: var(--maple-red);
    margin-top: 4px;
  }
  .contacts {
    list-style: none;
    margin-top: 14px;
    font-size: 14px;
    color: var(--ink);
    line-height: 1.45;
  }
  .contacts li { display: flex; justify-content: flex-end; align-items: center; gap: 8px; }
  .contacts svg { width: 12px; height: 12px; fill: var(--sky-blue); flex: none; }
  .contacts .address-line { padding-right: 20px; }

  .brand-mark {
    position: absolute;
    left: 36px;
    bottom: 34px;
    display: flex;
    align-items: center;
    gap: 10px;
  }
  .brand-mark__square { width: 22px; height: 22px; background: var(--sky-blue); }
  .brand-mark__name {
    font-family: "Montserrat", Arial, sans-serif;
    font-weight: 600;
    font-size: 20px;
    letter-spacing: 1px;
    color: var(--sky-blue);
  }
  .front-band {
    position: absolute;
    left: 0;
    right: 0;
    bottom: 0;
    height: 12px;
    background: var(--sky-blue);
  }

  /* back: brand side */
  .brand-block {
    position: absolute;
    top: 104px;
    left: 0;
    right: 0;
    display: flex;
    justify-content: center;
    align-items: center;
    gap: 14px;
  }
  .brand-block__square { width: 28px; height: 28px; background: var(--sky-blue); }
  .brand-block__name {
    font-family: "Montserrat", Arial, sans-serif;
    font-weight: 500;
    font-size: 26px;
    letter-spacing: 3px;
    color: var(--silver);
    text-transform: uppercase;
    white-space: nowrap;
  }
  .slogan {
    position: absolute;
    left: 0;
    right: 0;
    bottom: 64px;
    text-align: center;
    font-family: "Montserrat", Arial, sans-serif;
    font-weight: 500;
    font-size: 17px;
    letter-spacing: 1px;
    text-transform: uppercase;
  }
  .slogan__care { color: var(--sky-blue); }
  .slogan__years { color: var(--maple-red); }
</style>
</head>
<body>
  <section class="card card--front" aria-label="Contact side">
    <div class="rep">
      <h1 class="rep__name">Dale Kowalchuk</h1>
      <p class="rep__title">Managing Director</p>
      <ul class="contacts">
        <li>403-684-2093
          <svg viewBox="0 0 24 24" aria-hidden="true"><path d="M6.6 10.8a15 15 0 0 0 6.6 6.6l2.2-2.2c.3-.3.7-.4 1-.2 1.1.4 2.3.6 3.6.6.6 0 1 .4 1 1V20c0 .6-.4 1-1 1A17 17 0 0 1 3 4c0-.6.4-1 1-1h3.5c.6 0 1 .4 1 1 0 1.3.2 2.5.6 3.6.1.3 0 .7-.2 1z"/></svg></li>
        <li>403-684-2093
          <svg viewBox="0 0 24 24" aria-hidden="true"><path d="M7 1h10a2 2 0 0 1 2 2v18a2 2 0 0 1-2 2H7a2 2 0 0 1-2-2V3a2 2 0 0 1 2-2zm0 3v14h10V4z"/></svg></li>
        <li>dale@prairieshingleworks.com
          <svg viewBox="0 0 24 24" aria-hidden="true"><path d="M2 5h20v14H2zm2 2v.5l8 5 8-5V7l-8 5z"/></svg></li>
        <li>PrairieShingleWorks.com
          <svg viewBox="0 0 24 24" aria-hidden="true"><path d="M12 2a10 10 0 1 0 0 20 10 10 0 0 0 0-20zm0 2c.9 1.2 1.6 2.9 1.9 5h-3.8c.3-2.1 1-3.8 1.9-5zm-2.1 7h4.2a17 17 0 0 1 0 2H9.9a17 17 0 0 1 0-2zm.2 4h3.8c-.3 2.1-1 3.8-1.9 5-.9-1.2-1.6-2.9-1.9-5zM4.1 11h3.8a19 19 0 0 0 0 2H4.1a8 8 0 0 1 0-2zm12 0h3.8a8 8 0 0 1 0 2h-3.8a19 19 0 0 0 0-2z"/></svg></li>
        <li>2280 - 9 Avenue S.E. Calgary
          <svg viewBox="0 0 24 24" aria-hidden="true"><path d="M12 2a7 7 0 0 0-7 7c0 5 7 13 7 13s7-8 7-13a7 7 0 0 0-7-7zm0 9.5A2.5 2.5 0 1 1 12 6.5a2.5 2.5 0 0 1 0 5z"/></svg></li>
        <li class="address-line">Alberta T2G 4R7</li>
      </ul>
    </div>
    <div class="brand-mark">
      <span class="brand-mark__square" aria-hidden="true"></span>
      <span class="brand-mark__name">BRENT Roofing &amp; Siding</span>
    </div>
    <div class="front-band" aria-hidden="true"></div>
  </section>

  <section class="card card--back" aria-label="Brand side">
    <div class="brand-block">
      <span class="brand-block__square" aria-hidden="true"></span>
      <span class="brand-block__name">BRENT Roofing &amp; Siding</span>
    </div>
    <p class="slogan"><span class="slogan__care">Raised with care,</span> <span class="slogan__years">proven by years</span></p>
  </section>
</body>
</html>
```